A wine Label for a new brand of New Zealand Wine

We are looking for a Wine Label for our "Harbor Pine" brand of wines from North Otago New Zealand. We would like the label to perhaps use the HP as a logo and the rest up to the designer. We have our vineyards located in the Waitaki Valley New Zealand which is a southern region with mountains and a river flowing past our vineyard. Photos attached of Dramatic Landscape. Also attached is a basic outline of requirements for the front bottle of the label. The rear bottle label will contain writing about the wines background plus statutory regulations on Alc. Vol, bar code etc. Front Label size to be no Larger than 80mm deep by 100 mm wide. The label can be simple or graphic, whatever the designer chooses.
Target Market(s)
New Wine Brand
Look and feel
Each slider illustrates characteristics of the customer's brand and the style your logo design should communicate.

```html
<!DOCTYPE html>
<html lang="en">
<head>
<meta charset="utf-8">
<title>Harbor Pine – Pinot Gris Label</title>
<link rel="stylesheet" href="https://fonts.googleapis.com/css2?family=Cinzel:wght@600&family=Cormorant+Garamond:wght@500&family=IM+Fell+English:ital@1&display=swap">
<style>
  :root {
    --canvas: #f4f2ef;
    --label-light: #efe8df;
    --label-mid: #e4d9cc;
    --brand-brown: #7b4a25;
    --ink: #3b322c;
    --frame: #8a7d72;
    --land-pale: #e2d8cc;
    --land-mid: #c4b29f;
    --land-dark: #8f735a;
  }
  * { margin: 0; padding: 0; box-sizing: border-box; }
  html, body {
    width: 1200px; height: 1200px; overflow: hidden;
    background: var(--canvas);
  }
  .label {
    position: absolute; left: 100px; top: 112px;
    width: 1000px; height: 976px;
    background: linear-gradient(180deg, var(--label-light) 0%, var(--label-mid) 100%);
    text-align: center;
    color: var(--ink);
    font-family: "Cormorant Garamond", Georgia, serif;
  }
  .monogram {
    position: absolute; left: 50%; top: 76px;
    width: 210px; height: 228px; margin-left: -105px;
    border: 3px solid var(--frame);
    outline: 2px solid var(--frame); outline-offset: -14px;
    display: flex; align-items: center; justify-content: center;
    font-family: "Cinzel", Georgia, serif; font-weight: 600;
    font-size: 84px; color: var(--brand-brown);
  }
  .brand-name {
    position: absolute; left: 0; right: 0; top: 392px;
    font-family: "Cinzel", Georgia, serif; font-weight: 600;
    font-size: 96px; letter-spacing: 3px;
    color: var(--brand-brown);
  }
  .region {
    position: absolute; left: 0; right: 0; top: 530px;
    font-size: 31px; letter-spacing: 1px; text-transform: uppercase;
  }
  .varietal {
    position: absolute; left: 0; right: 0; top: 570px;
    font-size: 42px; letter-spacing: 2px; text-transform: uppercase;
  }
  .landscape {
    position: absolute; left: 0; right: 0; top: 640px; height: 170px;
    background:
      linear-gradient(180deg, rgba(239,232,223,1) 0%, rgba(239,232,223,0) 30%),
      linear-gradient(90deg, var(--land-mid) 0%, var(--land-pale) 40%, var(--land-dark) 60%, var(--land-mid) 100%);
  }
  .vintage {
    position: absolute; left: 0; right: 0; top: 832px;
    font-size: 34px; letter-spacing: 5px;
  }
  .origin {
    position: absolute; left: 0; right: 0; top: 890px;
    font-family: "IM Fell English", Georgia, serif; font-style: italic;
    font-size: 42px;
  }
</style>
</head>
<body>
  <main class="label">
    <div class="monogram">HP</div>
    <h1 class="brand-name">Harbor Pine</h1>
    <p class="region">Waitaki Valley—North Otago</p>
    <p class="varietal">Pinot Gris</p>
    <div class="landscape" role="img" aria-label="Sepia photograph of the Waitaki Valley vineyard with mountains and a row of poplar trees"></div>
    <p class="vintage">2015</p>
    <p class="origin">New Zealand Wine</p>
  </main>
</body>
</html>
```